Attic Lanterns (Progressive House Album)

Hey Guys,

I'm a music artist and I need a CD Cover done for my new album.The album is called "Attic Lanterns" and I really need something artistic, almost like a painting that reflects the name of the album.

Also please feel free to step out from the whole "almost like a painting" box, if your inner creator has something else to say. But preferably I'd have it as a painting...

Here are some keywords: Deep, Progressive, Lucid Dreaming, Ocean, Bedroom...

Please listen to the 3:30 demo of the album to get a better idea.

Thanks,

ToLa

Update:

I've uploaded a few images to kinda help you with the mood/colour tone and direction of what I want, Also, the script writing (I've uploaded a few examples), do it in white colour (left to right, going little bit upwards), preferably on the bottom of the image, simple, one touch, thin hand writing. Have it fading in size (bigger to smaller) as you get to the end of each word. Just like when you sign something, but have it written in two lines.

The whole image should be deep in colour with sort of a glow effect.

Must have
• Name of the album with Script writing,
Should not have
• No paper mosaic art. Image pieced together with cut outs from different sources.

```html
<!DOCTYPE html>
<html lang="en">
<head>
<meta charset="utf-8">
<title>Attic Lanterns – Album Cover</title>
<link rel="stylesheet" href="https://fonts.googleapis.com/css2?family=Allura&display=swap">
<style>
  :root {
    --backdrop: #2a2622;
    --deep-navy: #101a52;
    --midnight: #060a2a;
    --ocean-blue: #1e5fd0;
    --glow-cyan: #46c0f5;
    --nebula-pink: #d2427f;
    --nebula-rose: #9a3a8a;
    --haze-violet: #6e62b6;
    --haze-lilac: rgba(215, 200, 235, 0.75);
    --mist-white: rgba(235, 244, 255, 0.9);
    --script-white: #ffffff;
  }

  * { box-sizing: border-box; margin: 0; padding: 0; }

  html, body {
    width: 1200px;
    height: 750px;
    overflow: hidden;
    background: var(--backdrop);
  }

  .canvas {
    position: relative;
    width: 1200px;
    height: 750px;
    background: var(--backdrop);
  }

  .cover {
    position: absolute;
    top: 80px;
    width: 548px;
    height: 546px;
    overflow: hidden;
    background: var(--midnight);
  }

  .cover--front { left: 42px; }
  .cover--back  { left: 614px; }

  .cover__artwork {
    position: absolute;
    inset: 0;
  }

  .cover--front .cover__artwork {
    background:
      radial-gradient(ellipse 18% 9% at 52% 54%, var(--mist-white) 0%, rgba(190, 220, 255, 0.55) 50%, transparent 100%),
      radial-gradient(ellipse 28% 14% at 46% 63%, rgba(200, 225, 255, 0.7) 0%, rgba(140, 180, 240, 0.35) 55%, transparent 100%),
      radial-gradient(ellipse 55% 7% at 30% 52%, rgba(110, 190, 240, 0.45) 0%, transparent 100%),
      radial-gradient(ellipse 40% 8% at 80% 58%, rgba(220, 80, 140, 0.45) 0%, transparent 100%),
      radial-gradient(ellipse 45% 9% at 22% 60%, rgba(200, 70, 130, 0.35) 0%, transparent 100%),
      radial-gradient(ellipse 35% 10% at 60% 84%, rgba(150, 170, 230, 0.3) 0%, transparent 100%),
      radial-gradient(ellipse 9% 9% at 78% 30%, rgba(255, 255, 255, 0.85) 0%, transparent 100%),
      radial-gradient(ellipse 18% 14% at 22% 36%, var(--nebula-pink) 0%, transparent 100%),
      radial-gradient(ellipse 30% 24% at 30% 30%, rgba(180, 60, 120, 0.7) 0%, rgba(120, 50, 130, 0.3) 60%, transparent 100%),
      radial-gradient(ellipse 22% 14% at 68% 8%, var(--glow-cyan) 0%, transparent 100%),
      radial-gradient(ellipse 48% 32% at 72% 16%, rgba(40, 140, 230, 0.8) 0%, rgba(30, 90, 200, 0.4) 55%, transparent 100%),
      radial-gradient(ellipse 30% 22% at 40% 6%, var(--haze-lilac) 0%, transparent 100%),
      radial-gradient(ellipse 60% 30% at 50% 95%, rgba(30, 40, 110, 0.6) 0%, transparent 100%),
      linear-gradient(180deg, var(--haze-violet) 0%, var(--deep-navy) 42%, var(--midnight) 100%);
  }

  .cover--back .cover__artwork {
    background:
      radial-gradient(circle at 45% 79%, rgba(255, 255, 255, 0.95) 0%, rgba(220, 225, 255, 0.4) 3%, transparent 8%),
      radial-gradient(circle at 12% 72%, transparent 5%, rgba(200, 80, 90, 0.3) 6%, transparent 8%),
      radial-gradient(ellipse 14% 30% at 62% 32%, rgba(110, 210, 255, 0.75) 0%, transparent 100%),
      radial-gradient(ellipse 30% 55% at 60% 38%, rgba(60, 170, 245, 0.7) 0%, rgba(30, 100, 215, 0.35) 55%, transparent 100%),
      radial-gradient(ellipse 25% 12% at 72% 8%, var(--glow-cyan) 0%, transparent 100%),
      radial-gradient(ellipse 16% 14% at 18% 36%, var(--nebula-pink) 0%, transparent 100%),
      radial-gradient(ellipse 28% 24% at 22% 30%, rgba(170, 55, 125, 0.7) 0%, rgba(110, 50, 130, 0.3) 60%, transparent 100%),
      radial-gradient(ellipse 28% 22% at 36% 8%, var(--haze-lilac) 0%, transparent 100%),
      radial-gradient(ellipse 45% 10% at 55% 62%, rgba(150, 160, 225, 0.4) 0%, transparent 100%),
      radial-gradient(ellipse 40% 8% at 70% 82%, rgba(120, 110, 190, 0.3) 0%, transparent 100%),
      linear-gradient(180deg, var(--haze-violet) 0%, var(--ocean-blue) 28%, var(--deep-navy) 62%, var(--midnight) 100%);
  }

  .cover__title {
    position: absolute;
    font-family: "Allura", cursive;
    font-weight: 400;
    color: var(--script-white);
    line-height: 0.85;
    transform: rotate(-3deg);
    transform-origin: left top;
    text-shadow: 0 0 6px rgba(255, 255, 255, 0.3);
    white-space: nowrap;
  }

  .cover__title-line { display: block; }

  .cover--front .cover__title {
    left: 56px;
    top: 58px;
    font-size: 104px;
  }
  .cover--front .cover__title-line--second { padding-left: 168px; }

  .cover--back .cover__title {
    left: 52px;
    top: 402px;
    font-size: 62px;
  }
  .cover--back .cover__title-line--second { padding-left: 108px; }
</style>
</head>
<body>
  <main class="canvas">
    <section class="cover cover--front">
      <div class="cover__artwork" role="img" aria-label="Painted underwater night sky with pink and cyan nebula glow, a glowing white bed floating in swirling mist and sea spray"></div>
      <h1 class="cover__title">
        <span class="cover__title-line">Attic</span>
        <span class="cover__title-line cover__title-line--second">Lanterns</span>
      </h1>
    </section>

    <section class="cover cover--back">
      <div class="cover__artwork" role="img" aria-label="Painted underwater night sky with pink nebula, cyan light rays from the surface and a soft lens glow"></div>
      <h2 class="cover__title">
        <span class="cover__title-line">Attic</span>
        <span class="cover__title-line cover__title-line--second">Lanterns</span>
      </h2>
    </section>
  </main>
</body>
</html>
```